Please design a bold yet creative new "Folder Design" for our new school!

We need a bold folder design to attract new students/families between the ages of 10-14 and to attract new teachers to our school. Our school, Varlo Ridge Eastfield Academy, is one year old and located in Washington, DC. We are looking for a creative design that represents community, our logo/mascot and our commitment to and through college.

Target Market(s)

The target market for this folder is for young parents aged 20-25 and for recent college graduates, aged 22-30.

Industry/Entity Type

School

Colors
0255a3
33a6d7
ffffff

Requirements
Must have
• - Be formatted to the "TwinSleeve" indesign file. - http://pressnook.example/g/showStaticPage.do?page=download_templates-pres.html- Be a presentation folder, 9x12, with two pockets and a right pocket slit.- Be a bold color, consider navy blue for the background (white for contrast writing?)- Have our Varlo Ridge logo present somewhere on the front page.- Have our mascot highlighted somewhere.- Use our Varlo fonts, attached in file section.- Contact information on the inside left pocket should be there:Varlo Ridge Northeast AcademyT: 202-398-5477W: www.kippdc.orgA: 1375 Mount Olivet Road, NEWashington, DC 20099
Nice to have
• - Word art would be nice to have, like at this link: http://www.tanvo-pell.example/wp-content/uploads/2013/03/bookmark.jpg.- A "name box" on the front page could be nice to have. - "Founded in 2014" could be nice to have.- A creative
Should not have
• - It should not be busy.

```html
<!DOCTYPE html>
<html lang="en">
<head>
<meta charset="utf-8">
<title>Varlo Ridge Eastfield Academy – Presentation Folder</title>
<link href="https://fonts.googleapis.com/css2?family=Source+Sans+3:wght@300;400;600&display=swap" rel="stylesheet">
<style>
  :root {
    --stage: #3f6491;
    --navy-top: #3d669b;
    --navy-bottom: #21497e;
    --band: #f7f7f7;
    --ink: #3a3a3c;
    --brand-blue: #0255a3;
    --rule: rgba(255,255,255,0.55);
    --rule-soft: rgba(255,255,255,0.32);
    --tag: #d9e3ef;
    --fold: rgba(255,255,255,0.45);
  }
  * { box-sizing: border-box; margin: 0; padding: 0; }
  html, body { width: 1200px; height: 799px; overflow: hidden; }
  body {
    background: var(--stage);
    font-family: "Source Sans 3", "Gill Sans", sans-serif;
    position: relative;
  }
  .folder {
    position: absolute; left: 145px; top: 100px;
    width: 910px; height: 600px;
    background: linear-gradient(180deg, var(--navy-top), var(--navy-bottom));
    box-shadow: 0 10px 28px rgba(0,0,0,0.35);
  }
  .folder__band {
    position: absolute; left: 0; top: 0; width: 100%; height: 105px;
    background: var(--band);
  }
  .folder__fold {
    position: absolute; left: 455px; top: 0; width: 1px; height: 100%;
    background: var(--fold);
  }
  .panel { position: absolute; top: 105px; width: 455px; height: 495px; }
  .panel--back { left: 0; }
  .panel--front { left: 455px; }
  .panel__grid { position: absolute; inset: 0; }
  .brand {
    position: absolute; left: 475px; top: 28px;
    display: flex; align-items: center; gap: 12px;
    color: var(--ink); font-weight: 600;
  }
  .brand__dot { width: 30px; height: 30px; border-radius: 50%; background: var(--ink); }
  .brand__name { font-size: 28px; line-height: 1; letter-spacing: 0.5px; }
  .brand__name span { display: block; font-size: 16px; margin-top: 3px; letter-spacing: 0.2px; }
  .photo { position: absolute; border: 2px solid #fff; }
  .photo--graduate { left: 8px; top: 40px; width: 92px; height: 168px; background: linear-gradient(160deg, #c9c6bd, #3c4452); }
  .photo--student { left: 198px; top: 124px; width: 98px; height: 84px; background: linear-gradient(150deg, #e6a72b, #e9cf6a); }
  .photo--writer { left: 108px; top: 208px; width: 90px; height: 82px; background: linear-gradient(150deg, #d7c9b9, #4cb0c9); }
  .photo--classroom { left: 205px; top: 290px; width: 195px; height: 92px; background: linear-gradient(120deg, #33416b, #e0a34a 55%, #8ab55c); }
  .tagline {
    position: absolute; right: 50px; top: 395px; text-align: right;
    color: var(--tag); font-weight: 300;
  }
  .tagline__words { font-size: 26px; letter-spacing: 0.5px; word-spacing: 4px; }
  .tagline__founded { font-size: 15px; font-weight: 400; margin-top: 2px; }
  .web { position: absolute; bottom: 20px; font-size: 10px; color: var(--tag); }
  .panel--back .web { right: 38px; }
  .panel--front .web { right: 50px; }
</style>
</head>
<body>
  <main class="folder">
    <div class="folder__band"></div>
    <div class="folder__fold"></div>

    <div class="brand">
      <div class="brand__dot"></div>
      <div class="brand__name">Varlo Ridge<span>Eastfield Academy</span></div>
    </div>

    <section class="panel panel--back">
      <svg class="panel__grid" width="455" height="495" viewBox="0 0 455 495">
        <g stroke="var(--rule-soft)" stroke-width="1.5" fill="none">
          <polyline points="250,40 445,40"/>
          <line x1="250" y1="40" x2="250" y2="395"/>
          <line x1="345" y1="40" x2="345" y2="360"/>
          <line x1="65" y1="130" x2="360" y2="115"/>
          <line x1="155" y1="45" x2="160" y2="395"/>
          <rect x="70" y="215" width="200" height="180"/>
          <line x1="70" y1="300" x2="445" y2="285"/>
          <line x1="70" y1="215" x2="445" y2="195"/>
          <line x1="160" y1="215" x2="165" y2="395"/>
          <line x1="345" y1="195" x2="350" y2="360"/>
        </g>
      </svg>
      <div class="web">www.varloridge.example</div>
    </section>

    <section class="panel panel--front">
      <svg class="panel__grid" width="455" height="495" viewBox="0 0 455 495">
        <g stroke="var(--rule)" stroke-width="2" fill="none">
          <polyline points="100,40 195,40 195,125"/>
          <line x1="100" y1="125" x2="400" y2="125"/>
          <line x1="295" y1="40" x2="295" y2="125"/>
          <line x1="295" y1="125" x2="300" y2="208"/>
          <line x1="375" y1="115" x2="420" y2="115"/>
          <line x1="300" y1="40" x2="300" y2="120"/>
          <polyline points="296,208 405,200 410,290 205,290"/>
          <line x1="8" y1="290" x2="110" y2="290"/>
          <line x1="105" y1="290" x2="110" y2="375"/>
          <line x1="310" y1="208" x2="312" y2="290"/>
          <line x1="100" y1="208" x2="108" y2="208"/>
        </g>
      </svg>
      <div class="photo photo--graduate" role="img" aria-label="Photo of a smiling graduate in cap and gown"></div>
      <div class="photo photo--student" role="img" aria-label="Photo of a smiling young student"></div>
      <div class="photo photo--writer" role="img" aria-label="Photo of a student writing at a desk"></div>
      <div class="photo photo--classroom" role="img" aria-label="Photo of a teacher and students reading together in class"></div>

      <div class="tagline">
        <div class="tagline__words">learn &nbsp;|&nbsp; lead &nbsp;|&nbsp; innovate</div>
        <div class="tagline__founded">Founded in 2014</div>
      </div>
      <div class="web">www.varloridge.example</div>
    </section>
  </main>
</body>
</html>
```